Social Media App Needs PPT Template

We need a PowerPoint template for a new social media company based in the DC area called "Bold Ledger." We provide an interactive digital platform for executives to share actionable advice. We would like to see designs that use our orange logo color as an accent, but are mainly grey, white, and black. The final design should communicate clean, chic, modern, and professional.

Target Market(s)

Executives

Industry/Entity Type

Information Technology

Font styles to use
Sans Serif

Colors
f78f20
fbe7d2
ffffff
000000
e8e8e8
757575

Requirements
Must have
• My project must have title page and many options for the body of the ppt (graphs, tables, etc). It also needs to be easy to modify. I must have someone who is experienced in creating powerpoint templates.
Nice to have
• It would be nice to have a very modern and clean design that includes the logo on every page, but still leaves a lot of room for the content of the slide
Should not have
• My design project should not look to busy.

```html
<!DOCTYPE html>
<html lang="en">
<head>
<meta charset="utf-8">
<title>Bold Ledger – Title Slide</title>
<link href="https://fonts.googleapis.com/css2?family=Lato:wght@300;700&display=swap" rel="stylesheet">
<style>
  :root {
    --board-grey: #cbcbcb;
    --slide-navy: #222b3a;
    --accent-orange: #f39220;
    --text-white: #ffffff;
    --text-soft: #e8e8e8;
  }
  * { margin: 0; padding: 0; box-sizing: border-box; }
  html, body {
    width: 1200px; height: 960px; overflow: hidden;
    background: var(--board-grey);
    font-family: "Lato", sans-serif;
  }
  .board { position: relative; width: 1200px; height: 960px; }
  .page-label {
    position: absolute; top: 66px; left: 0; width: 1236px;
    text-align: center; font-weight: 300; font-size: 29px;
    color: var(--text-white); letter-spacing: 0.5px;
  }
  .slide {
    position: absolute; left: 120px; top: 143px;
    width: 958px; height: 718px;
    background: var(--slide-navy); overflow: hidden;
  }
  .slide-art { position: absolute; inset: 0; width: 958px; height: 718px; }
  .brand-name {
    position: absolute; left: 670px; top: 372px; width: 244px;
    text-align: center; color: var(--text-white);
    font-weight: 700; font-size: 38px; letter-spacing: 6px;
    text-transform: uppercase; line-height: 1.15;
  }
  .tagline-rule {
    position: absolute; left: 197px; width: 725px; height: 2px;
    background: var(--accent-orange);
  }
  .tagline-rule.top { top: 567px; }
  .tagline-rule.bottom { top: 631px; }
  .tagline {
    position: absolute; left: 197px; top: 582px; width: 725px;
    text-align: center; color: var(--text-soft);
    font-weight: 300; font-size: 31px; white-space: nowrap;
  }
  .web-address {
    position: absolute; right: 48px; top: 650px;
    color: var(--text-soft); font-weight: 300; font-size: 19px;
  }
</style>
</head>
<body>
<main class="board">
  <p class="page-label">Page 1</p>
  <section class="slide">
    <svg class="slide-art" viewBox="0 0 1198 898" preserveAspectRatio="none">
      <defs>
        <linearGradient id="photoTone" x1="0" y1="0" x2="1" y2="0.6">
          <stop offset="0" stop-color="#bfe8f8"/>
          <stop offset="0.2" stop-color="#2f6f9c"/>
          <stop offset="0.45" stop-color="#0d1a28"/>
          <stop offset="0.7" stop-color="#3a2a22"/>
          <stop offset="1" stop-color="#0b0b0e"/>
        </linearGradient>
        <radialGradient id="keyGlow" cx="0.45" cy="0.75" r="0.4">
          <stop offset="0" stop-color="#9fbad6" stop-opacity="0.55"/>
          <stop offset="1" stop-color="#9fbad6" stop-opacity="0"/>
        </radialGradient>
      </defs>
      <g role="img" aria-label="Photo of a hand typing on a backlit laptop keyboard">
        <path class="photo-area" d="M0,0 H981 L798,139 L863,166 C650,450 300,650 0,694 Z" fill="url(#photoTone)"/>
        <path d="M0,0 H981 L798,139 L863,166 C650,450 300,650 0,694 Z" fill="url(#keyGlow)"/>
      </g>
      <path class="growth-arrow" d="M0,694 C300,650 650,450 863,166 L798,139 L981,0 L1015,214 L945,189 C760,450 420,670 0,697 Z" fill="var(--accent-orange)"/>
    </svg>
    <div class="brand-name">Bold<br>Ledger</div>
    <div class="tagline-rule top"></div>
    <p class="tagline">interactive digital platform to share actionable advice</p>
    <div class="tagline-rule bottom"></div>
    <p class="web-address">www.boldledger.com</p>
  </section>
</main>
</body>
</html>
```